BRIGHT RIVER POWER.

I'd like my business logo.
contact name: Dennis Halvorsen
phone:0438759164
email: info@brightriverpower.net.au
website: www.brightriverpower.net.au

services:
solar
battery storage
LED lighting
energy saving solutions
general electrical
I'd like the design to look professional

Target Market(s)

Everyone

Industry/Entity Type

Business

Contact Information for Business Card

as described above

Requirements
Must have
• Id like the colours and the design to work well with my logo.

```html
<!DOCTYPE html>
<html lang="en">
<head>
<meta charset="utf-8">
<title>Bright River Power – Business Card</title>
<link href="https://fonts.googleapis.com/css2?family=Lato:wght@400;700;900&display=swap" rel="stylesheet">
<style>
  :root {
    --backdrop: #2b2b2b;
    --card-white: #fafafa;
    --leaf-green: #74ad35;
    --leaf-green-dark: #5f9426;
    --brand-green: #6aab2e;
    --sun-orange: #e8920f;
    --ink: #1e1e1e;
    --paper-text: #ffffff;
    --muted-white: #e9f3de;
  }
  * { margin: 0; padding: 0; box-sizing: border-box; }
  html, body {
    width: 1200px; height: 873px; overflow: hidden;
    background: var(--backdrop);
    font-family: "Lato", Arial, sans-serif;
  }
  .canvas {
    position: relative; width: 1200px; height: 873px;
    display: flex; align-items: center; justify-content: center;
  }
  .business-card {
    position: relative; width: 880px; height: 538px;
    background: var(--card-white);
    border-radius: 22px; overflow: hidden;
  }
  .card-wave { position: absolute; inset: 0; width: 100%; height: 100%; }
  .contact-person {
    position: absolute; top: 48px; right: 44px; text-align: right;
  }
  .contact-person .person-name {
    color: var(--brand-green); font-weight: 900; font-size: 27px; line-height: 1.1;
  }
  .contact-person .person-role {
    color: var(--ink); font-size: 16px; font-weight: 400; margin-top: 2px;
  }
  .brand {
    position: absolute; left: 56px; top: 150px;
    display: flex; align-items: center; gap: 16px;
  }
  .brand-dot {
    width: 58px; height: 58px; border-radius: 50%; background: var(--sun-orange);
  }
  .brand-name {
    color: var(--brand-green); font-weight: 900; font-size: 40px; letter-spacing: 1px;
    line-height: 1;
  }
  .services {
    position: absolute; right: 40px; top: 214px; text-align: right;
    color: var(--ink);
  }
  .services-title {
    display: inline-block; color: var(--muted-white); font-weight: 700; font-size: 20px;
    border-bottom: 2px solid var(--muted-white); padding-bottom: 2px; margin-right: 22px;
    margin-bottom: 6px;
  }
  .services-list { list-style: none; }
  .services-list li {
    font-weight: 700; font-size: 18px; line-height: 29px;
    display: flex; justify-content: flex-end; align-items: center; gap: 12px;
  }
  .services-list li::after {
    content: ""; width: 9px; height: 9px; border-radius: 50%; background: var(--muted-white);
  }
  .contact-details {
    position: absolute; left: 44px; top: 380px; list-style: none;
  }
  .contact-details li {
    display: flex; align-items: center; gap: 12px;
    color: var(--paper-text); font-size: 24px; line-height: 44px;
  }
  .contact-icon {
    width: 32px; height: 32px; border-radius: 50%;
    background: rgba(255,255,255,0.85);
    display: flex; align-items: center; justify-content: center;
  }
  .contact-icon svg { width: 18px; height: 18px; fill: var(--leaf-green-dark); }
</style>
</head>
<body>
<main class="canvas">
  <section class="business-card" aria-label="Bright River Power business card">
    <svg class="card-wave" viewBox="0 0 880 538" preserveAspectRatio="none" aria-hidden="true">
      <path fill="var(--sun-orange)" d="M0,300 C200,352 420,332 560,240 C680,162 800,128 880,122 L880,538 L0,538 Z"/>
      <path fill="var(--leaf-green)" d="M0,316 C200,368 432,348 572,258 C690,182 800,146 880,142 L880,538 L0,538 Z"/>
    </svg>

    <div class="contact-person">
      <div class="person-name">Dennis Halvorsen</div>
      <div class="person-role">Owner / Founder</div>
    </div>

    <div class="brand">
      <span class="brand-dot"></span>
      <span class="brand-name">BRIGHT RIVER POWER</span>
    </div>

    <div class="services">
      <div class="services-title">Our Services:</div>
      <ul class="services-list">
        <li>Solar</li>
        <li>LED Lighting</li>
        <li>Battery Storage</li>
        <li>General Electrical</li>
        <li>Energy Saving Solutions</li>
      </ul>
    </div>

    <ul class="contact-details">
      <li>
        <span class="contact-icon"><svg viewBox="0 0 24 24"><path d="M6.6 10.8a15.2 15.2 0 0 0 6.6 6.6l2.2-2.2a1 1 0 0 1 1-.25 11.4 11.4 0 0 0 3.6.57 1 1 0 0 1 1 1V20a1 1 0 0 1-1 1A17 17 0 0 1 3 4a1 1 0 0 1 1-1h3.5a1 1 0 0 1 1 1c0 1.25.2 2.45.57 3.57a1 1 0 0 1-.25 1z"/></svg></span>
        0438759164
      </li>
      <li>
        <span class="contact-icon"><svg viewBox="0 0 24 24"><path d="M3 5h18a1 1 0 0 1 1 1v12a1 1 0 0 1-1 1H3a1 1 0 0 1-1-1V6a1 1 0 0 1 1-1zm1 2.2V17h16V7.2l-8 5.3z M4.6 7l7.4 4.9L19.4 7z"/></svg></span>
        info@brightriverpower.net.au
      </li>
      <li>
        <span class="contact-icon"><svg viewBox="0 0 24 24"><path d="M10.6 13.4a1 1 0 0 1 0-1.4l3-3a1 1 0 1 1 1.4 1.4l-3 3a1 1 0 0 1-1.4 0zM8 20a4 4 0 0 1-2.8-6.8l2.5-2.5 1.4 1.4-2.5 2.5a2 2 0 0 0 2.8 2.8l2.5-2.5 1.4 1.4-2.5 2.5A4 4 0 0 1 8 20zm8.3-6.7-1.4-1.4 2.5-2.5a2 2 0 0 0-2.8-2.8l-2.5 2.5-1.4-1.4 2.5-2.5a4 4 0 0 1 5.6 5.6z"/></svg></span>
        www.brightriverpower.net.au
      </li>
    </ul>
  </section>
</main>
</body>
</html>
```